K & R Acre Works. Business card design

We need a business card designed for a new business. We have a bulldozer and tractor service. We clear land and make wildlife food plots. We provide disking, bush hogging, and site prep services.
I have attached an image of a business card that I like and would like my business cards to look similar.

Target Market(s)

anyone needing bulldozer and/or tractor services

Industry/Entity Type

Business

Contact Information for Business Card

K & R Acre Works, Operated by 7-T-Ranch
Wade Colton
601-472-3358
wcr4817@fieldmail-example.com

Font styles to use
Sans Serif

Colors

Designer to choose colors to be used in the design.

Requirements
Must have
• image of tractor and bulldozer
• Land Clearing
• Wildlife food plots
• Bush Hogging
• Disking
• Site prep
Nice to have
• i have included a image of a business card that i like. I would like mine to be similar.

```html
<!DOCTYPE html>
<html lang="en">
<head>
<meta charset="utf-8">
<title>K &amp; R Acre Works — Business Card</title>
<link rel="stylesheet" href="https://fonts.googleapis.com/css2?family=Roboto:wght@400;500&family=Roboto+Condensed:wght@500;700&display=swap">
<style>
  :root {
    --page-bg: #e4e4e2;
    --card-bg: #f4f4f2;
    --olive: #8c8c2c;
    --olive-band: #9d9d3a;
    --orange-band: #b5601b;
    --brown: #6a3f17;
    --brown-band: #6b4420;
    --text: #4a4a48;
    --rule: #4e4e4c;
  }
  * { margin: 0; padding: 0; box-sizing: border-box; }
  html, body { width: 1200px; height: 960px; overflow: hidden; }
  body { background: var(--page-bg); position: relative; font-family: "Roboto", Arial, sans-serif; }

  .business-card {
    position: absolute; left: 300px; top: 310px;
    width: 600px; height: 342px;
    background: var(--card-bg);
    border-radius: 16px;
    overflow: hidden;
    box-shadow: 0 2px 6px rgba(0,0,0,0.18);
  }

  .brand { position: absolute; right: 33px; top: 34px; text-align: right; }
  .brand-name {
    display: flex; align-items: center; justify-content: flex-end; gap: 6px;
    font-family: "Roboto Condensed", Arial, sans-serif; font-weight: 700;
    font-size: 17px; letter-spacing: 0.3px; color: var(--brown);
    text-transform: uppercase; line-height: 1;
  }
  .brand-mark { width: 12px; height: 12px; background: var(--olive); }
  .brand-tagline {
    margin-top: 4px;
    font-family: "Roboto Condensed", Arial, sans-serif; font-weight: 700;
    font-size: 8.6px; color: #2f2f2d; text-transform: uppercase; letter-spacing: 0.1px;
  }

  .service-photo { position: absolute; top: 68px; height: 68px; }
  .photo-bulldozer {
    left: 354px; width: 115px;
    background: linear-gradient(180deg, #6f7d5a 0%, #8a8a5c 45%, #b8a44a 60%, #6e6a5a 100%);
  }
  .photo-tractor {
    left: 475px; width: 92px;
    background: linear-gradient(180deg, #7f8a58 0%, #8f9360 40%, #b8552e 62%, #8c8a5c 100%);
  }

  .owner { position: absolute; left: 33px; top: 190px; }
  .owner-name {
    font-family: "Roboto Condensed", Arial, sans-serif; font-weight: 500;
    font-size: 22px; color: var(--olive); text-transform: uppercase; line-height: 1.1;
  }
  .owner-title {
    font-family: "Roboto Condensed", Arial, sans-serif; font-weight: 500;
    font-size: 15px; color: var(--brown); text-transform: uppercase; line-height: 1.2;
  }

  .divider { position: absolute; left: 34px; right: 30px; top: 242px; height: 1px; background: var(--rule); }

  .contact-list { position: absolute; left: 33px; top: 260px; list-style: none; }
  .contact-list li {
    display: flex; align-items: center; gap: 6px;
    font-size: 14px; color: var(--text); height: 18px;
  }
  .contact-icon { width: 13px; height: 13px; fill: var(--olive); flex: none; }

  .service-list { position: absolute; right: 30px; top: 260px; text-align: right; }
  .service-row { font-size: 14px; color: var(--text); height: 18px; line-height: 18px; }
  .dot { display: inline-block; width: 5px; height: 5px; border-radius: 50%; background: var(--olive); vertical-align: middle; margin: 0 3px 0 6px; }
  .dot-inline { margin: 0 2px; }

  .color-band { position: absolute; left: 0; right: 0; bottom: 0; height: 10px; display: flex; gap: 2px; background: #fff; }
  .band-olive { width: 197px; background: var(--olive-band); }
  .band-orange { width: 203px; background: var(--orange-band); }
  .band-brown { flex: 1; background: var(--brown-band); }
</style>
</head>
<body>
  <article class="business-card">
    <header class="brand">
      <div class="brand-name"><span class="brand-mark"></span>K &amp; R Acre Works</div>
      <div class="brand-tagline">For all of your land improvement needs</div>
    </header>

    <div class="service-photo photo-bulldozer" role="img" aria-label="Photo of a yellow bulldozer clearing land"></div>
    <div class="service-photo photo-tractor" role="img" aria-label="Photo of an orange tractor with a mower in a field"></div>

    <div class="owner">
      <div class="owner-name">Wade Colton</div>
      <div class="owner-title">Owner</div>
    </div>

    <div class="divider"></div>

    <ul class="contact-list">
      <li>
        <svg class="contact-icon" viewBox="0 0 16 16" aria-hidden="true"><path d="M3.6 1.2l2.3 2.6-1.3 1.9c.9 2 2.5 3.6 4.6 4.6l1.9-1.3 2.6 2.3-1.3 2.3C7.2 14.6 1.4 8.8 1.4 2.5z"/></svg>
        601-472-3358
      </li>
      <li>
        <svg class="contact-icon" viewBox="0 0 16 16" aria-hidden="true"><path d="M1 3h14v1.2L8 8.6 1 4.2z"/><path d="M1 5.6l7 4.4 7-4.4V13H1z"/></svg>
        wcr4817@fieldmail-example.com
      </li>
      <li>
        <svg class="contact-icon" viewBox="0 0 16 16" aria-hidden="true"><circle cx="8" cy="8" r="7"/><path d="M4 5.5c1.5-.5 2.5.5 3 1.5s-1 2-.5 3.5S5 12.5 4.5 12M10 3c-.5 1 .5 2 1.5 2.2s1 1.5 2.5 1.3M9.5 9.5c1 0 2 .8 1.8 2.5" stroke="#f4f4f2" stroke-width="1.2" fill="none"/></svg>
        kracreworks-example.com
      </li>
    </ul>

    <div class="service-list">
      <div class="service-row">Land Clearing<span class="dot"></span></div>
      <div class="service-row">Wildlife food plots<span class="dot"></span></div>
      <div class="service-row">Bush Hogging<span class="dot dot-inline"></span>Disking&nbsp;&nbsp; Site prep<span class="dot"></span></div>
    </div>

    <div class="color-band">
      <span class="band-olive"></span><span class="band-orange"></span><span class="band-brown"></span>
    </div>
  </article>
</body>
</html>
```